Weightloss company needs Business Card

We want a business card that is clean and professional, yet portrays that we are a friendly, innovative, and versatile program designed to fit the needs of our clients.
I would like there to be 2 sides, one side having an appointment card, and the other side containing the logo and business information. There can be decorations on both sides. The logo is attached.

Target Market(s)

Men and women 40-60

Industry/Entity Type

Business

Contact Information for Business Card

Font styles to use
Sans Serif

Requirements
Must have
• The logo, space for business information
Nice to have
• The colors in the logo
Should not have
• No pictures of people or food

```html
<!DOCTYPE html>
<html lang="en">
<head>
<meta charset="utf-8">
<title>Harbor Lane Health – Business Card</title>
<link href="https://fonts.googleapis.com/css2?family=Open+Sans:ital,wght@0,400;0,600;0,700;1,400&display=swap" rel="stylesheet">
<style>
  :root{
    --red:#f1153f;
    --red-deep:#e30f39;
    --cyan:#1fd3f2;
    --white:#ffffff;
    --ink:#3a3a3a;
    --rule:#9a9a9a;
    --bg:#e9e7e3;
  }
  *{margin:0;padding:0;box-sizing:border-box}
  html,body{width:1200px;height:950px;overflow:hidden}
  body{background:var(--bg);font-family:"Open Sans",sans-serif;position:relative}
  .card{position:absolute;left:220px;width:760px;height:434px;background:var(--white);
    border-radius:18px;overflow:hidden;box-shadow:0 6px 18px rgba(0,0,0,.18)}
  .card--front{top:30px}
  .card--back{top:490px}

  /* front */
  .front-art{position:absolute;inset:0;width:760px;height:434px}
  .brand{position:absolute;left:56px;top:80px;display:flex;align-items:center;gap:12px}
  .brand__dot{width:18px;height:18px;border-radius:50%;background:var(--cyan)}
  .brand__name{color:var(--red);font-weight:600;font-size:28px;letter-spacing:.3px}
  .identity{position:absolute;left:56px;top:236px;color:var(--white)}
  .identity__name{font-size:30px;font-weight:600;letter-spacing:.5px;line-height:1.1}
  .identity__role{font-size:18px;margin-top:2px}
  .identity__addr{font-size:18px;line-height:1.35;margin-top:16px}
  .divider{position:absolute;left:318px;top:228px;width:1px;height:150px;background:rgba(255,255,255,.7)}
  .contacts{position:absolute;left:340px;top:228px;list-style:none;color:var(--white);font-size:18px}
  .contacts li{display:flex;align-items:center;gap:10px;height:30px}
  .contacts svg{width:16px;height:16px;flex:none}

  /* back */
  .appt{position:absolute;inset:0;color:var(--ink)}
  .appt__title{position:absolute;right:56px;top:36px;color:var(--red);font-weight:700;font-size:30px}
  .field{position:absolute;display:flex;align-items:flex-end;font-size:20px;color:var(--red)}
  .field__line{flex:1;border-bottom:2px dotted var(--rule);margin-left:8px;height:20px}
  .field--name{left:56px;top:110px;width:420px}
  .field--date{left:56px;top:160px;width:420px}
  .field--time{left:420px;top:250px;width:284px}
  .field__suffix{font-size:12px;color:var(--red);margin-left:6px}
  .days{position:absolute;left:56px;top:250px;display:grid;grid-template-columns:repeat(3,100px);row-gap:18px;list-style:none;font-size:18px;color:var(--red)}
  .days li{display:flex;align-items:center;gap:6px}
  .box{width:16px;height:16px;border:1.5px solid var(--ink)}
  .appt__note{position:absolute;left:56px;right:56px;bottom:36px;font-style:italic;font-size:14px;line-height:1.45;color:var(--ink)}
</style>
</head>
<body>

<section class="card card--front" aria-label="Business card front">
  <svg class="front-art" viewBox="0 0 760 434" aria-hidden="true">
    <defs>
      <linearGradient id="band" x1="0" y1="0" x2="1" y2="0">
        <stop offset="0" stop-color="#f1153f"/><stop offset="1" stop-color="#e30f39"/>
      </linearGradient>
    </defs>
    <rect x="600" y="0" width="160" height="200" fill="var(--cyan)"/>
    <rect x="0" y="200" width="760" height="234" fill="url(#band)"/>
    <circle cx="680" cy="185" r="100" fill="var(--red)"/>
    <path d="M572 150 A112 112 0 0 1 770 130" fill="none" stroke="#fff" stroke-width="7"/>
  </svg>

  <div class="brand">
    <span class="brand__dot"></span>
    <span class="brand__name">Harbor Lane Health</span>
  </div>

  <div class="identity">
    <p class="identity__name">DANA MORROW</p>
    <p class="identity__role">CEO/FOUNDER</p>
    <p class="identity__addr">1420 Willow Court<br>Boise, Idaho 83702</p>
  </div>
  <span class="divider"></span>
  <ul class="contacts">
    <li><svg viewBox="0 0 16 16"><path d="M3 1h3l1 4-2 1c1 2 3 4 5 5l1-2 4 1v3c0 1-1 2-2 2C7 15 1 9 1 3c0-1 1-2 2-2z" fill="#fff"/></svg>555 214 7630</li>
    <li><svg viewBox="0 0 16 16"><rect x="4" y="1" width="8" height="14" rx="1.5" fill="#fff"/><rect x="5.5" y="3" width="5" height="8" fill="var(--red)"/></svg>555 390 1184</li>
    <li><svg viewBox="0 0 16 16"><rect x="1" y="3" width="14" height="10" fill="#fff"/><path d="M1 3l7 6 7-6" fill="none" stroke="var(--red)" stroke-width="1.5"/></svg>hello@harborlane.com</li>
    <li><svg viewBox="0 0 16 16"><circle cx="8" cy="8" r="7" fill="#fff"/><path d="M1 8h14M8 1c3 3 3 11 0 14M8 1c-3 3-3 11 0 14" fill="none" stroke="var(--red)" stroke-width="1"/></svg>www.harborlane.com</li>
  </ul>
</section>

<section class="card card--back" aria-label="Appointment card back">
  <div class="appt">
    <h2 class="appt__title">Next Appointment</h2>
    <div class="field field--name">Name :<span class="field__line"></span></div>
    <div class="field field--date">Date :<span class="field__line"></span></div>
    <ul class="days">
      <li>Mon <span class="box"></span></li>
      <li>Tue <span class="box"></span></li>
      <li>Wed <span class="box"></span></li>
      <li>Thu <span class="box"></span></li>
      <li>Fri <span class="box"></span></li>
      <li>Sat <span class="box"></span></li>
    </ul>
    <div class="field field--time">Time :<span class="field__line"></span><span class="field__suffix">AM/PM</span></div>
    <p class="appt__note">Please give 24 hours notice if you are unable to keep your appointment or<br>a cancellation fee may be charged.</p>
  </div>
</section>

</body>
</html>
```